Law Firm Website

We are a small California based law firm specializing in business, corporate and litigation matters. We need to have our website redesigned. We are looking for a new and fresh look for our site, keeping in mind that we are a law firm.
What we don't want:
**the traditional "gavel" and "scales of justice" look
**anything too crazy
What we do want:
**sophisticated yet modern and fresh corporate look and feel
**samples of websites we really like:
http://www.tarnwellhope.example
http://www.marrowgate.example/
we also like:
http://www.fenwoodastley.example/
http://www.qz.example/
http://www.brenhollow.example/
http://www.pvdn.example
http://www.nqrlaw.example/
The content will be whatever is currently on our website (www.okabelawgroup.example). We will be selecting the winner based on originality and keeping the above requirements in mind. Please note that the photos that you use will be the ones that we will be using, so choose wisely because the photos will make a difference.
Target Market(s)
Corporate clients
Industry/Entity Type
Law Firm
Look and feel

```html
<!DOCTYPE html>
<html lang="en">
<head>
<meta charset="utf-8">
<title>Okabe Law Group, LLP</title>
<link rel="stylesheet" href="https://fonts.googleapis.com/css2?family=Open+Sans:wght@400;600;700&display=swap">
<style>
  :root {
    --brand-blue: #0a78c2;
    --navy: #0d3f7e;
    --ink: #222222;
    --body-text: #5f5f5f;
    --muted: #7a7a7a;
    --rule: #e2e2e2;
    --panel: #f1f1f1;
    --footer-bg: #eeeeee;
    --logo-bg: #000000;
    --white: #ffffff;
  }
  * { box-sizing: border-box; margin: 0; padding: 0; }
  html, body { width: 1200px; height: 1090px; overflow: hidden; }
  body {
    position: relative;
    background: var(--white);
    font-family: "Open Sans", Arial, sans-serif;
    color: var(--ink);
  }

  /* Header */
  .site-header {
    position: absolute; left: 0; top: 0; width: 1200px; height: 162px;
    background: linear-gradient(#ffffff 55%, #f3f3f3);
    border-top: 1px solid #dddddd;
    border-bottom: 1px solid #d6d6d6;
  }
  .brand {
    position: absolute; left: 99px; top: 0; width: 301px; height: 162px;
    background: var(--logo-bg);
    display: flex; flex-direction: column; align-items: center; justify-content: center; gap: 14px;
  }
  .brand-mark { width: 56px; height: 56px; background: var(--brand-blue); }
  .brand-name { color: var(--white); font-size: 23px; font-weight: 400; letter-spacing: .2px; }

  .account-links {
    position: absolute; left: 782px; top: 42px;
    font-size: 14px; color: var(--brand-blue);
  }
  .account-links .divider { color: #8a8a8a; margin: 0 12px; }

  .search {
    position: absolute; left: 943px; top: 35px; width: 157px; height: 33px;
    border: 1px solid #cfcfcf; border-radius: 3px; background: var(--white);
  }
  .search-placeholder { position: absolute; left: 14px; top: 8px; font-size: 13px; color: #999; }
  .search-sep { position: absolute; left: 124px; top: 5px; width: 1px; height: 21px; background: #d5d5d5; }
  .search-icon { position: absolute; left: 131px; top: 6px; }

  .main-nav {
    position: absolute; left: 451px; top: 106px;
    display: flex; gap: 0; font-size: 14.5px; color: var(--ink); text-transform: uppercase;
  }
  .main-nav a { color: inherit; text-decoration: none; position: relative; }
  .main-nav .nav-home { margin-right: 45px; color: var(--brand-blue); }
  .main-nav .nav-home::after {
    content: ""; position: absolute; left: 0; top: 21px; width: 43px; height: 35px;
    background: linear-gradient(#4aa8e8, #0b76c9);
  }
  .main-nav .nav-about { margin-right: 45px; }
  .main-nav .nav-services { margin-right: 45px; }
  .main-nav .nav-practice { margin-right: 45px; }
  .main-nav .nav-links { margin-right: 45px; }

  /* Hero slider */
  .hero {
    position: absolute; left: 99px; top: 172px; width: 1002px; height: 460px;
    background: linear-gradient(180deg, #7f9ed0 0%, #9aafd6 32%, #a8a0c4 52%, #c39aae 62%, #4e5268 75%, #3d4c66 88%, #2c3447 100%);
  }
  .hero-title {
    position: absolute; left: 34px; top: 34px;
    color: var(--white); font-size: 25.5px; font-weight: 700; line-height: 36px;
    text-transform: uppercase; text-shadow: 0 1px 3px rgba(0,0,0,.45);
  }
  .hero-text {
    position: absolute; left: 34px; top: 110px; width: 500px;
    color: #111; font-size: 15px; line-height: 25px; font-weight: 600;
  }
  .slide-arrow {
    position: absolute; top: 208px; width: 42px; height: 42px; border-radius: 50%;
    background: rgba(255,255,255,.85);
  }
  .slide-arrow svg { position: absolute; left: 13px; top: 12px; }
  .slide-prev { left: 20px; }
  .slide-next { left: 939px; }

  /* Welcome */
  .welcome { position: absolute; left: 101px; top: 660px; width: 724px; }
  .welcome h1 { font-size: 20.5px; font-weight: 600; color: var(--brand-blue); text-transform: uppercase; }
  .welcome p { margin-top: 12px; font-size: 13.5px; line-height: 23px; color: var(--body-text); }
  .btn-more {
    display: inline-block; margin-top: 12px; padding: 0 12px; height: 32px; line-height: 30px;
    font-size: 13.5px; color: #444; background: linear-gradient(#f7f7f7, #e9e9e9);
    border: 1px solid #d6d6d6; border-radius: 3px;
  }
  .divider-line { position: absolute; left: 99px; top: 883px; width: 723px; height: 1px; background: var(--rule); }

  .call-line {
    position: absolute; left: 155px; top: 900px;
    display: flex; align-items: center; font-size: 19px; color: #555;
  }
  .call-line .call-label { color: var(--brand-blue); margin: 0 12px 0 8px; }
  .call-line .sep { margin: 0 16px; }

  /* News */
  .news { position: absolute; left: 861px; top: 667px; width: 240px; height: 277px; background: var(--panel); border-radius: 3px; }
  .news-header {
    height: 42px; line-height: 42px; padding-left: 14px; border-radius: 3px 3px 0 0;
    background: linear-gradient(#0f5fae, #0b3d7e);
    color: var(--white); font-size: 18px; font-weight: 700; text-transform: uppercase;
  }
  .news-item { position: relative; padding: 17px 8px 0 37px; }
  .news-item svg { position: absolute; left: 12px; top: 23px; }
  .news-title { font-size: 13.5px; line-height: 21px; color: var(--navy); }
  .news-date { margin-top: 6px; font-size: 13px; color: var(--ink); }
  .news-item + .news-item { padding-top: 14px; }
  .news-item + .news-item svg { top: 20px; }

  /* Footer */
  .site-footer {
    position: absolute; left: 0; top: 989px; width: 1200px; height: 101px;
    background: var(--footer-bg); border-top: 1px solid #d8d8d8;
  }
  .footer-nav { position: absolute; left: 99px; top: 24px; font-size: 13.5px; color: var(--muted); font-weight: 600; }
  .footer-nav .sep { margin: 0 12px; font-weight: 400; }
  .copyright { position: absolute; left: 99px; top: 57px; font-size: 13.5px; color: var(--muted); font-weight: 600; }
  .social { position: absolute; left: 1045px; top: 39px; display: flex; gap: 7px; }
  .social span { width: 24px; height: 24px; border-radius: 3px; }
  .social .social-a { background: #3b5a9a; }
  .social .social-b { background: #35b5e6; }
</style>
</head>
<body>
  <header class="site-header">
    <div class="brand">
      <span class="brand-mark"></span>
      <span class="brand-name">Okabe Law Group, LLP</span>
    </div>

    <div class="account-links"><span>REGISTER</span><span class="divider">|</span><span>LOGIN</span></div>

    <div class="search">
      <span class="search-placeholder">Search</span>
      <span class="search-sep"></span>
      <svg class="search-icon" width="20" height="20" viewBox="0 0 20 20" aria-hidden="true">
        <circle cx="8" cy="8" r="6" fill="none" stroke="#8c8c8c" stroke-width="2.4"/>
        <line x1="12.5" y1="12.5" x2="18" y2="18" stroke="#8c8c8c" stroke-width="3" stroke-linecap="round"/>
      </svg>
    </div>

    <nav class="main-nav">
      <a class="nav-home" href="#">Home</a>
      <a class="nav-about" href="#">About us</a>
      <a class="nav-services" href="#">Services</a>
      <a class="nav-practice" href="#">Practice areas</a>
      <a class="nav-links" href="#">Links</a>
      <a href="#">Contact us</a>
    </nav>
  </header>

  <section class="hero" role="img" aria-label="Photo of a cable-stayed bridge over calm water at dusk">
    <h2 class="hero-title">Suspendisse pharetra imperdiet dui<br>consectetur congue varius</h2>
    <p class="hero-text">Donec nec sem vel tortor egestas vulputate. Morbi mattis pellen-tesque ligula in laoreet. Phasellus fringilla urna ac nisl ornare tempor. Proin facilisis, urna in congue scelerisque, orci lectus dignissim</p>
    <span class="slide-arrow slide-prev">
      <svg width="16" height="18" viewBox="0 0 16 18" aria-hidden="true"><polyline points="11,2 4,9 11,16" fill="none" stroke="#9a9a9a" stroke-width="1.8"/></svg>
    </span>
    <span class="slide-arrow slide-next">
      <svg width="16" height="18" viewBox="0 0 16 18" aria-hidden="true"><polyline points="5,2 12,9 5,16" fill="none" stroke="#9a9a9a" stroke-width="1.8"/></svg>
    </span>
  </section>

  <section class="welcome">
    <h1>Welcome to Okabe Law Group</h1>
    <p>Nulla posuere risus id ligula porttitor tempus. Maecenas id arcu nec arcu commodo porttitor consectetur sit amet eros. Cras ut nibh velit. Praesent nisi odio, varius eu ipsum ultrices, venenatis pharetra nunc. Ut eget lacinia nibh. Vestibulum dictum, nibh vitae convallis imperdiet, elit turpis pharetra mauris, fringilla vehicula sapien nulla eget nulla. Phasellus risus neque, eleifend at malesuada et, ornare sed nulla. Sed lacinia, metus ac faucibus sollicitudin, odio neque porttitor lectus, at ultrices magna massa non lectus.</p>
    <span class="btn-more">Read more</span>
  </section>

  <div class="divider-line"></div>

  <div class="call-line">
    <svg width="28" height="24" viewBox="0 0 28 24" aria-hidden="true">
      <path d="M4 3 L9 2 L12 8 L9 10 Q12 16 17 18 L19 15 L25 18 L24 22 Q12 24 5 13 Q2 7 4 3 Z" fill="#0a78c2"/>
      <path d="M17 5 Q22 6 23 11" fill="none" stroke="#0a78c2" stroke-width="1.6"/>
      <path d="M17 9 Q19 9.5 19.5 12" fill="none" stroke="#0a78c2" stroke-width="1.6"/>
    </svg>
    <span class="call-label">Call us</span>
    <span>-&nbsp;&nbsp;Phone :&nbsp; (555) 010-1200</span>
    <span class="sep">/</span>
    <span>Facsimile : (555) 010-1277</span>
  </div>

  <aside class="news">
    <div class="news-header">Latest news</div>
    <div class="news-item">
      <svg width="14" height="12" viewBox="0 0 14 12" aria-hidden="true"><polyline points="2,2 6,6 2,10" fill="none" stroke="#888" stroke-width="1.5"/><line x1="11" y1="0" x2="11" y2="12" stroke="#bbb"/></svg>
      <div class="news-title">Donec magna ante, congue ut nunc nec, aliquam elementum augue quis leo.</div>
      <div class="news-date">January 2, 2014</div>
    </div>
    <div class="news-item">
      <svg width="14" height="12" viewBox="0 0 14 12" aria-hidden="true"><polyline points="2,2 6,6 2,10" fill="none" stroke="#888" stroke-width="1.5"/><line x1="11" y1="0" x2="11" y2="12" stroke="#bbb"/></svg>
      <div class="news-title">Donec magna ante, congue ut nunc nec, aliquam elementum augue quis leo.</div>
      <div class="news-date">January 2, 2014</div>
    </div>
  </aside>

  <footer class="site-footer">
    <div class="footer-nav">Home<span class="sep">|</span>About us<span class="sep">|</span>Services<span class="sep">|</span>Practice Areas<span class="sep">|</span>Links<span class="sep">|</span>Contact us</div>
    <div class="copyright">Copyright &nbsp;©&nbsp; 2014 &nbsp; Okabe Law Group. &nbsp; All rights reserved.</div>
    <div class="social" aria-label="Social links">
      <span class="social-a"></span>
      <span class="social-b"></span>
    </div>
  </footer>
</body>
</html>
```